Letterhead designs for Property Management firm

Would like to see some different letterhead/envelope designs We are a residential property management company. We would like to see designs that utilize blue/grays/black

```html
<!DOCTYPE html>
<html lang="en">
<head>
<meta charset="utf-8">
<title>Harborview Property Management — Stationery</title>
<link href="https://fonts.googleapis.com/css2?family=Didact+Gothic&family=Roboto:wght@400&display=swap" rel="stylesheet">
<style>
  :root {
    --stage: #dcdcdc;
    --paper: #f6f6f6;
    --brand-blue: #0054a6;
    --ink: #222222;
    --body-text: #4a4a4a;
    --rule: #555555;
  }
  * { box-sizing: border-box; margin: 0; padding: 0; }
  html, body { width: 1200px; height: 877px; overflow: hidden; }
  body {
    background: var(--stage);
    position: relative;
    font-family: "Didact Gothic", "Century Gothic", sans-serif;
    color: var(--body-text);
  }
  .sheet { position: absolute; background: var(--paper); }
  .edge-bar { position: absolute; left: 0; top: 0; height: 100%; }

  /* Letterhead */
  .letterhead { left: 68px; top: 64px; width: 528px; height: 742px; }
  .wordmark {
    position: absolute;
    font-family: "Didact Gothic", sans-serif;
    color: var(--brand-blue);
    line-height: 1.15;
    letter-spacing: 0.5px;
    text-align: center;
  }
  .letterhead .wordmark { left: 48px; top: 116px; width: 110px; font-size: 12px; }
  .salutation { position: absolute; left: 47px; top: 272px; font-size: 14px; color: #333; }
  .letter-body { position: absolute; left: 47px; top: 311px; width: 439px; }
  .letter-body p {
    font-size: 7.6px; line-height: 11.4px; margin-bottom: 11.4px; text-align: justify;
  }
  .closing { position: absolute; left: 47px; top: 549px; font-size: 7.6px; }
  .signature {
    position: absolute; left: 44px; top: 582px; width: 94px; height: 38px;
    background: linear-gradient(90deg, rgba(0,84,166,0.18), rgba(0,84,166,0.06));
    border-radius: 3px;
  }
  .contact-list {
    position: absolute; left: 47px; top: 665px; list-style: none;
    font-family: "Roboto", sans-serif; font-size: 7.8px; color: #444;
  }
  .contact-list li { display: flex; align-items: center; height: 10.4px; gap: 4px; }
  .contact-list svg { width: 7px; height: 7px; fill: var(--brand-blue); }
  .footer-rule { position: absolute; left: 110px; top: 670px; width: 376px; height: 1px; background: var(--rule); }
  .footer-address {
    position: absolute; right: 42px; top: 677px; text-align: right;
    font-family: "Roboto", sans-serif; font-size: 7.8px; line-height: 10.4px; color: #444;
  }

  /* Envelope back */
  .envelope-back { left: 614px; top: 269px; width: 531px; height: 241px; }
  .flap {
    position: absolute; left: 0; top: 0; width: 531px; height: 74px;
    background: var(--brand-blue);
    border-radius: 0 0 38px 38px;
  }
  .flap-name {
    position: absolute; left: 0; right: 0; top: 28px; text-align: center;
    color: #ffffff; font-size: 12px; letter-spacing: 1px;
  }

  /* Envelope front */
  .envelope-front { left: 612px; top: 562px; width: 534px; height: 242px; }
  .envelope-front .wordmark { left: 34px; top: 30px; width: 104px; font-size: 11.5px; }
  .return-address {
    position: absolute; left: 34px; top: 96px; width: 104px; text-align: center;
    font-family: "Roboto", sans-serif; font-size: 7.6px; line-height: 9.6px; color: #444;
  }
</style>
</head>
<body>

<section class="sheet letterhead" aria-label="Letterhead">
  <svg class="edge-bar" width="10" height="742" viewBox="0 0 10 742" aria-hidden="true">
    <polygon points="0,0 10,0 10,102 0,116" fill="var(--ink)"/>
    <polygon points="0,116 10,102 10,742 0,742" fill="var(--brand-blue)"/>
  </svg>

  <div class="wordmark">HARBORVIEW<br>PROPERTY<br>MANAGEMENT</div>

  <p class="salutation">Dear Mr. Avery,</p>

  <div class="letter-body">
    <p>Lorem ipsum dolor sit amet, consectetur adipiscing elit. Donec orci purus, luctus vitae dignissim eu, iaculis sed purus. Vivamus faucibus, ipsum nec aliquet viverra, leo mauris condimentum ligula, sit amet sagittis enim ligula quis arcu. Nam egestas tortor id nisi porttitor mattis. In tortor ante, ultricies in suscipit a, tempus non massa. Vivamus et auctor mi. Fusce vel massa nulla. Phasellus nec eros mauris, et scelerisque orci.</p>
    <p>Donec malesuada orci vitae nulla accumsan porta a id massa. Quisque accumsan iaculis magna sit amet fringilla. Maecenas consequat, magna eget tincidunt semper, odio nibh rutrum mi, id feugiat ante nisi eu risus. Vestibulum nunc orci, rhoncus a placerat in, ultricies in mi. Cras mattis varius eros, vel fringilla nisi suscipit eget. Quisque scelerisque sagittis nulla at porttitor.</p>
    <p>Sed id augue vitae urna euismod commodo aliquet a quam. Pellentesque arcu velit, cursus et malesuada ut, consequat et diam. Nullam erat sem, rhoncus id ullamcorper vitae, rhoncus et arcu. In ultricies ultricies nulla, ut rutrum nisi iaculis at. Donec eu magna a metus ornare faucibus. Fusce aliquet faucibus ultricies. Morbi semper, est id tincidunt gravida, sem arcu adipiscing lacus, ac bibendum nulla leo eu purus. Quisque nec diam sed risus consectetur a ccumsan quis quis nibh. Vestibulum id purus lorem.</p>
    <p>It is a long established fact that a reader will be distracted by the readable content of a page when looking at its layout. The point of using Lorem Ipsum is that it has a more-or-less normal distribution of letters, as opposed to using 'Content here, content here', making it look like readable English. Many desktop publishing packages</p>
  </div>

  <p class="closing">Sincerely,</p>
  <div class="signature" role="img" aria-label="Handwritten signature of Daniel Reyes in blue ink"></div>

  <ul class="contact-list">
    <li><svg viewBox="0 0 10 10"><path d="M2 0.5l2 2-1 1.3c.6 1.3 1.6 2.3 2.9 2.9L7.2 5.7l2.3 2-1.2 1.8C4.5 9.3.7 5.5.5 1.7z"/></svg>555 214 7730</li>
    <li><svg viewBox="0 0 10 10"><path d="M2.5 0h5v10h-5zM3.5 1v7h3V1z"/></svg>555 318 4421</li>
    <li><svg viewBox="0 0 10 10"><path d="M2.5 0h5v3h-5zM0 3.5h10v4H8V10H2V7.5H0zM3 6v3h4V6z"/></svg>555 902 6615</li>
    <li><svg viewBox="0 0 10 10"><path d="M0 2h10v6H0zM1 3l4 2.8L9 3z" fill-rule="evenodd"/></svg>hello@harborviewpm.com</li>
  </ul>
  <div class="footer-rule"></div>
  <div class="footer-address">2140 Cedar Crest Road<br>Fairbanks, Alaska 99701<br>www.harborviewpm.com</div>
</section>

<section class="sheet envelope-back" aria-label="Envelope back">
  <div class="flap"><p class="flap-name">HARBORVIEW</p></div>
</section>

<section class="sheet envelope-front" aria-label="Envelope front">
  <svg class="edge-bar" width="10" height="242" viewBox="0 0 10 242" aria-hidden="true">
    <polygon points="0,0 10,0 10,86 0,100" fill="var(--ink)"/>
    <polygon points="0,100 10,86 10,242 0,242" fill="var(--brand-blue)"/>
  </svg>
  <div class="wordmark">HARBORVIEW<br>PROPERTY<br>MANAGEMENT</div>
  <div class="return-address">2140 Cedar Crest Road<br>Fairbanks, Alaska 99701</div>
</section>

</body>
</html>
```